Cover for Lanterns Along the Quiet Shore of Being

Cover for a book that describes everything that happens to a person, from pre-birth life plans through growing in compassion and wisdom to death and living in the afterlife. The information is revealed in messages from people living in the life after this life. The title is Lessons Gathered From Every Season of Your Existence: Shared by Voices Dwelling Beyond the Veil. Author is T. Wesley Prandt. Book size is 6 by 9.

Target Market(s)

General

Font styles to use
Serif

```html
<!DOCTYPE html>
<html lang="en">
<head>
<meta charset="UTF-8">
<title>Lanterns Along the Quiet Shore of Being – Book Cover</title>
<link href="https://fonts.googleapis.com/css2?family=Marcellus&family=Montserrat:ital,wght@0,400;0,700;1,400&display=swap" rel="stylesheet">
<style>
  :root{
    --navy:#0c1426;
    --gold:#f2b01e;
    --gold-light:#ffd25a;
    --gold-deep:#c98a10;
    --white:#ffffff;
    --body:#e8ebf2;
    --sky-light:#dcefff;
    --sky-mid:#4f8fd6;
    --sky-deep:#163a78;
  }
  *{margin:0;padding:0;box-sizing:border-box}
  html,body{width:1200px;height:828px;overflow:hidden;background:var(--navy)}
  .cover{position:relative;width:1200px;height:828px;background:var(--navy);overflow:hidden;font-family:"Montserrat",sans-serif}

  .gold-text{
    background:linear-gradient(180deg,var(--gold-light) 0%,var(--gold) 45%,var(--gold-deep) 100%);
    -webkit-background-clip:text;background-clip:text;color:transparent;
  }

  /* back cover */
  .back-heading{position:absolute;left:44px;width:472px;top:40px;text-align:center;font-family:"Marcellus",serif;color:var(--gold);font-size:24px;line-height:31px}
  .back-blurb{position:absolute;left:44px;width:472px;top:127px;color:var(--body);font-size:11.2px;line-height:13.5px;text-align:justify}
  .rule{position:absolute;left:47px;width:466px;height:1.5px;background:linear-gradient(90deg,transparent,var(--gold) 20%,var(--gold) 80%,transparent)}
  .rule.top{top:283px}
  .rule.bottom{top:366px}
  .quote{position:absolute;left:80px;width:399px;top:300px;color:var(--body);font-size:11.2px;line-height:13.5px;font-style:italic;text-align:justify}
  .quote-by{position:absolute;right:721px;top:334px;color:var(--body);font-size:11.2px}
  .quote-by b{font-weight:700}
  .back-author{position:absolute;left:44px;width:472px;top:392px;text-align:center;font-family:"Marcellus",serif;color:var(--gold);font-size:25px;letter-spacing:4px}
  .author-photo{position:absolute;left:50px;top:437px;width:144px;height:210px;background:var(--white)}
  .author-bio{position:absolute;left:210px;width:306px;top:435px;color:var(--body);font-size:11.2px;line-height:13.5px;text-align:justify}
  .more-info{position:absolute;left:47px;top:740px;color:var(--body);font-size:11.2px}
  .site{position:absolute;left:47px;top:759px;width:189px;height:19px;background:var(--gold);color:var(--navy);font-size:10.6px;font-style:italic;line-height:19px;padding-left:6px}

  /* spine */
  .spine-title{position:absolute;left:566px;top:46px;width:72px;height:420px;writing-mode:vertical-rl;font-family:"Marcellus",serif;color:var(--gold);font-size:21px;line-height:30px}
  .spine-title span{display:block}
  .spine-author{position:absolute;left:582px;top:522px;writing-mode:vertical-rl;font-family:"Marcellus",serif;color:var(--white);font-size:30px;letter-spacing:1px}

  /* front cover */
  .sky{position:absolute;left:560px;top:330px;width:640px;height:498px;
    background:
      radial-gradient(ellipse 45% 38% at 56% 62%,var(--sky-light) 0%,rgba(220,239,255,.7) 30%,rgba(79,143,214,.5) 60%,transparent 85%),
      radial-gradient(ellipse 70% 65% at 56% 65%,var(--sky-mid) 0%,var(--sky-deep) 55%,transparent 90%);
  }
  .front{position:absolute;left:675px;width:472px;text-align:center;font-family:"Marcellus",serif}
  .t-big{top:40px;font-size:100px;line-height:100px;letter-spacing:1px}
  .t-small{top:137px;font-size:31px;color:var(--gold)}
  .t-mid{top:176px;font-size:74px;line-height:74px;letter-spacing:2px}
  .divider{position:absolute;left:693px;top:268px;width:454px;height:2px}
  .divider::before,.divider::after{content:"";position:absolute;top:0;width:200px;height:2px;background:var(--gold)}
  .divider::before{left:0}
  .divider::after{right:0}
  .divider-mark{position:absolute;left:221px;top:-6px;width:12px;height:12px;background:var(--gold);transform:rotate(45deg)}
  .t-last{top:290px;font-size:60px;line-height:60px;letter-spacing:2px}
  .subtitle{top:370px;color:var(--white);font-size:30px;line-height:42px}
  .front-author{top:740px;color:var(--white);font-size:42px;letter-spacing:1px}
</style>
</head>
<body>
<div class="cover">

  <!-- back cover -->
  <h2 class="back-heading">LESSONS gathered from every season<br>OF YOUR EXISTENCE</h2>
  <p class="back-blurb">Lorem ipsum dolor sit amet, consectetur adipisicing elit, sed do eiusmod tempor incididunt ut labore et dolore magna aliqua. Ut enim ad minim veniam, quis nostrud exercitation ullamco laboris nisi ut aliquip ex ea commodo consequat. Duis aute irure dolor in reprehenderit in voluptate velit esse cillum dolore eu fugiat nulla pariatur. Excepteur sint occaecat cupidatat non proident, sunt in culpa qui officia deserunt mollit anim id est laborum. Sed ut perspiciatis unde omnis iste natus error sit voluptatem accusantium doloremque laudantium, totam rem aperiam, eaque ipsa quae ab illo inventore veritatis et quasi architecto beatae vitae dicta sunt explicabo. Nemo enim ipsam.</p>
  <div class="rule top"></div>
  <p class="quote">“Lorem ipsum dolor sit amet, consectetur adipisicing elit, sed do eiusmod tempor incididunt ut labore et dolore magna aliqua.”</p>
  <p class="quote-by"><b>- Elena,</b> Author Lorem ipsum</p>
  <div class="rule bottom"></div>
  <h3 class="back-author">T. WESLEY PRANDT</h3>
  <div class="author-photo" role="img" aria-label="Author portrait placeholder"></div>
  <p class="author-bio">Lorem ipsum dolor sit amet, consectetur adipisicing elit, sed do eiusmod tempor incididunt ut labore et dolore magna aliqua. Ut enim ad minim veniam, quis nostrud exercitation ullamco laboris nisi ut aliquip ex ea commodo consequat. Duis aute irure dolor in reprehenderit in voluptate velit esse cillum dolore eu fugiat nulla pariatur. Excepteur sint occaecat cupidatat non proident, sunt in culpa qui officia deserunt mollit anim id est laborum. Sed ut perspiciatis unde omnis iste natus error sit voluptatem accusantium doloremque laudantium, totam rem aperiam, eaque ipsa quae ab illo inventore veritatis et quasi architecto beatae vitae dicta sunt explicabo. Nemo enim ipsam voluptatem quia voluptas sit aspernatur aut odit aut fugit, sed quia consequuntur magni dolores eos qui ratione voluptatem sequi nesciunt.</p>
  <p class="more-info">For more information, Please visit</p>
  <p class="site">www.quietshorebooks.com</p>

  <!-- spine -->
  <div class="spine-title">
    <span>LESSONS gathered from every season</span>
    <span>OF YOUR EXISTENCE</span>
  </div>
  <div class="spine-author">T. WESLEY PRANDT</div>

  <!-- front cover -->
  <div class="sky" role="img" aria-label="Radiant sky with glowing clouds and light beams around a doorway at the top of a stairway"></div>
  <h1 class="front t-big gold-text">LESSONS</h1>
  <p class="front t-small">gathered from every season</p>
  <p class="front t-mid gold-text">OF YOUR</p>
  <div class="divider"><span class="divider-mark"></span></div>
  <p class="front t-last gold-text">EXISTENCE</p>
  <p class="front subtitle">Shared by Voices Dwelling<br>Beyond the Veil</p>
  <p class="front front-author">T. WESLEY PRANDT</p>

</div>
</body>
</html>
```